Elegant Business Card with Logo and Picture

Please create a business card that has the Logo colors add Gold and turquoise / use the attached logo - I would like a beautiful Business Card - Please make sure it's printed on both sides / Picture can go on one side Logo other
www.velmoragrove.com
614-372-0583
Lina Suzette Brolin
linasb@quorvamail.com
Life Coach
Thessing Certified Teacher / Life Coach / Interior Designer
Transformational Retreats

Target Market(s)

Women Men General

Industry/Entity Type

Life Coaching

Contact Information for Business Card

www.velmoragrove.com
614-372-0583
Lina Suzette Brolin
Life Coach
Thessing Certified Teacher / Yoga Teacher / Interior Designer

Font styles to use
Serif
Decorative

Colors
33a6d6
e34197
ffc214

Requirements
Must have
• Quality Paper and touch /
Nice to have
• Beautiful Touch and feel
Should not have
• needs to be elegant

```html
<!DOCTYPE html>
<html lang="en">
<head>
<meta charset="utf-8">
<title>Velmora Grove Coaching — Business Card</title>
<link href="https://fonts.googleapis.com/css2?family=Zilla+Slab:wght@300;400;500&family=Allura&display=swap" rel="stylesheet">
<style>
  :root {
    --backdrop: #2b2e33;
    --paper: #ffffff;
    --turquoise: #3bbfc2;
    --gold: #c9972e;
    --gold-light: #f1d47a;
    --gold-mid: #d9ab3c;
    --gold-dark: #a8761c;
    --ink: #5a5a5a;
    --ink-dark: #3a3222;
  }
  * { box-sizing: border-box; margin: 0; padding: 0; }
  html, body {
    width: 1200px; height: 900px; overflow: hidden;
    background: var(--backdrop);
    font-family: "Zilla Slab", Georgia, serif;
  }
  .sheet {
    width: 1200px; height: 900px;
    display: flex; flex-direction: column; align-items: center; justify-content: center;
    gap: 48px;
  }
  .card {
    position: relative;
    width: 660px; height: 377px;
    border-radius: 4px;
    overflow: hidden;
    box-shadow: 0 14px 30px rgba(0,0,0,.45);
  }

  /* Front side */
  .card-front { background: var(--paper); }
  .front-tab {
    position: absolute; left: 0; top: 0;
    width: 10px; height: 26px; background: var(--gold);
  }
  .front-brand {
    position: absolute; left: 38px; top: 30px;
    font-weight: 400; font-size: 25px; letter-spacing: 3px;
    text-transform: uppercase; color: var(--turquoise);
  }
  .front-name-row {
    position: absolute; left: 40px; top: 92px;
    display: flex; align-items: baseline; gap: 8px;
  }
  .person-name {
    font-family: "Allura", cursive;
    font-size: 38px; color: var(--gold);
  }
  .divider-bar { color: var(--turquoise); font-size: 22px; font-weight: 300; }
  .person-role { color: var(--turquoise); font-size: 22px; font-weight: 300; }
  .credentials {
    position: absolute; left: 40px; top: 142px;
    font-size: 19px; font-weight: 300; color: var(--ink); line-height: 1.25;
  }
  .credentials .sep { color: var(--turquoise); }
  .front-rule {
    position: absolute; left: 40px; top: 206px;
    width: 620px; height: 1px; background: var(--turquoise);
  }
  .contact-list {
    position: absolute; left: 40px; top: 222px;
    list-style: none; font-size: 18px; font-weight: 300; color: var(--ink);
  }
  .contact-list li { display: flex; align-items: center; gap: 10px; height: 30px; }
  .contact-icon { width: 16px; height: 16px; flex: none; }
  .portrait {
    position: absolute; right: 0; bottom: 0;
    width: 260px; height: 250px;
    background: linear-gradient(180deg, #f4efe9 0%, #e9c98f 38%, #e58aa0 72%, #d3566f 100%);
  }

  /* Back side */
  .card-back {
    background: linear-gradient(120deg, var(--gold-dark) 0%, var(--gold-mid) 30%, var(--gold-light) 55%, var(--gold-mid) 78%, var(--gold-dark) 100%);
  }
  .back-mark {
    position: absolute; left: 50%; top: 92px; transform: translateX(-50%);
    display: flex; flex-direction: column; align-items: center;
  }
  .back-circle {
    width: 62px; height: 62px; border-radius: 50%;
    border: 2px solid var(--gold-light);
    margin-bottom: 18px;
  }
  .back-brand {
    font-weight: 500; font-size: 32px; letter-spacing: 4px;
    text-transform: uppercase; color: var(--turquoise); white-space: nowrap;
  }
  .back-rule {
    width: 230px; height: 1px; background: #fff3c8; margin-top: 58px;
  }
  .tagline {
    margin-top: 10px; font-size: 20px; font-weight: 400; color: var(--ink-dark);
  }
</style>
</head>
<body>
<main class="sheet">

  <section class="card card-front" aria-label="Business card front">
    <div class="front-tab"></div>
    <div class="front-brand">Velmora Grove Coaching</div>

    <div class="front-name-row">
      <span class="person-name">Lina Suzette Brolin</span>
      <span class="divider-bar">|</span>
      <span class="person-role">Life Coach</span>
    </div>

    <div class="credentials">
      Thessing Certified Teacher <span class="sep">|</span> Yoga Teacher<br>
      Interior Designer
    </div>

    <div class="front-rule"></div>

    <ul class="contact-list">
      <li>
        <svg class="contact-icon" viewBox="0 0 16 16"><circle cx="8" cy="8" r="7.5" fill="var(--turquoise)"/><path d="M5.2 4.2l1.4-.2.7 1.8-.9.7a5 5 0 0 0 2.4 2.4l.7-.9 1.8.7-.2 1.4c-3.3.3-6.2-2.6-5.9-5.9z" fill="#fff"/></svg>
        614-372-0583
      </li>
      <li>
        <svg class="contact-icon" viewBox="0 0 16 16"><circle cx="8" cy="8" r="7.5" fill="var(--turquoise)"/><rect x="4" y="5" width="8" height="6" fill="none" stroke="#fff" stroke-width="1"/><path d="M4 5l4 3.2L12 5" fill="none" stroke="#fff" stroke-width="1"/></svg>
        linasb@quorvamail.com
      </li>
      <li>
        <svg class="contact-icon" viewBox="0 0 16 16"><circle cx="8" cy="8" r="7.5" fill="var(--turquoise)"/><circle cx="8" cy="8" r="4.2" fill="none" stroke="#fff" stroke-width="1"/><path d="M3.8 8h8.4M8 3.8c-2 2.4-2 6 0 8.4M8 3.8c2 2.4 2 6 0 8.4" fill="none" stroke="#fff" stroke-width=".9"/></svg>
        www.velmoragrove.com
      </li>
    </ul>

    <div class="portrait" role="img" aria-label="Portrait photo of Lina Suzette Brolin"></div>
  </section>

  <section class="card card-back" aria-label="Business card back">
    <div class="back-mark">
      <div class="back-circle"></div>
      <div class="back-brand">Velmora Grove Coaching</div>
      <div class="back-rule"></div>
      <div class="tagline">Transformational Retreats</div>
    </div>
  </section>

</main>
</body>
</html>
```